Flat Belly Design Graphics for Social

I want to create 9 social media graphics (new Instagram size 4:5 (1080 x 1350 pixels) focusing on our Flat Belly Graphics, using the pics attached. Use the attached pics, NO RANDOM STOCK PHOTOGRAPHY. For the color scheme of the graphics, the color palette is attached. YOU MUST POST ALL 9 GRAPHICS IN ONE ENTRY.
Using the 3 titles below, create one set of graphics. 1) with all text, then for the others, use the pictures as detailed below in IMPORTANT:
1. Ten-Week Bright Morning Reboot
2. The Quick Garden Kitchen Menu Guide
3. Studio Habits for Lasting Energy Past Midlife - Zero Gym Needed
IMPORTANT:
Only use RK Pic 1 and RK Pic 2 with the title, Ten-Week Bright Morning Reboot
Only use meal plan1 and meal plan2 pics with the title, Quick Garden Kitchen Menu Guide
Only use studio habits 1 and studio habits 2 pics with the title, Studio Habits for Lasting Energy Past Midlife - Zero Gym Needed
women over 40

```html
<!DOCTYPE html>
<html lang="en">
<head>
<meta charset="utf-8">
<title>Social Graphics Set</title>
<link href="https://fonts.googleapis.com/css2?family=Oswald:wght@600;700&family=Yellowtail&display=swap" rel="stylesheet">
<style>
  :root {
    --board: #5b5b5b;
    --pink: #e8a0b5;
    --pink-soft: #f9dde4;
    --pink-pale: #fde9ee;
    --green: #2f4b48;
    --cream: #fce6ec;
    --food-a: #c86a3a;
    --food-b: #4a3a2c;
    --sky: #74c9db;
    --kitchen: #6b4a34;
  }
  * { box-sizing: border-box; margin: 0; padding: 0; }
  html, body { width: 967px; height: 1200px; overflow: hidden; background: var(--board); }
  .board { position: relative; width: 967px; height: 1200px; }
  .tile { position: absolute; width: 296px; height: 368px; overflow: hidden; }
  .col-1 { left: 11px; } .col-2 { left: 333px; } .col-3 { left: 656px; }
  .row-1 { top: 8px; } .row-2 { top: 415px; } .row-3 { top: 816px; }

  .photo { position: absolute; inset: 0; }
  .photo-food { background: radial-gradient(circle at 30% 30%, #d9463a 0%, transparent 35%), radial-gradient(circle at 75% 80%, #e8b23a 0%, transparent 30%), linear-gradient(135deg, var(--food-a), var(--food-b) 55%, #6c8a3a); }
  .photo-friends-sky { background: radial-gradient(ellipse at 50% 40%, #d9a98d 0%, #a5795e 30%, transparent 60%), var(--sky); }
  .photo-friends-light { background: radial-gradient(ellipse at 45% 40%, #a87a5e 0%, #5a3d2e 35%, transparent 65%), linear-gradient(#f3f1ee, #e4e0dc); }
  .photo-kitchen { background: radial-gradient(ellipse at 50% 60%, #f1ece6 0%, #c7b8aa 25%, transparent 50%), linear-gradient(var(--kitchen), #8a6a52 60%, #5a4232); }
  .cutout { position: absolute; border-radius: 40% 40% 10% 10%; background: linear-gradient(#4a3227 0%, #a4715a 30%, #f3efec 45%, #efe9e6 80%, #2b2b2b 100%); }

  .panel { position: absolute; display: flex; flex-direction: column; align-items: center; justify-content: center; text-align: center; }
  .panel-pink { background: rgba(232,160,181,0.92); }
  .panel-green { background: var(--green); }

  .t { font-family: "Oswald", sans-serif; font-weight: 700; text-transform: uppercase; line-height: 1; white-space: nowrap; letter-spacing: 0.2px; }
  .script { font-family: "Yellowtail", cursive; font-weight: 400; line-height: 1.1; white-space: nowrap; }
  .c-green { color: var(--green); } .c-cream { color: var(--cream); } .c-pink { color: var(--pink); }

  .fade-pink { position: absolute; left: 0; right: 0; bottom: 0; height: 200px; background: linear-gradient(rgba(232,160,181,0) 0%, var(--pink) 28%); }
  .fade-green { position: absolute; left: 0; right: 0; bottom: 0; height: 195px; background: linear-gradient(rgba(47,75,72,0) 0%, var(--green) 30%); }
  .bottom-text { position: absolute; left: 0; right: 0; bottom: 20px; display: flex; flex-direction: column; }
  .soft-bg { background: linear-gradient(var(--pink-pale), var(--pink-soft)); }
  .arc { position: absolute; left: -30px; right: -30px; top: 198px; bottom: -10px; border-radius: 50% 50% 0 0 / 40px 40px 0 0; background: linear-gradient(var(--pink-soft), var(--pink) 40%); }
</style>
</head>
<body>
<main class="board">

  <!-- Row 1: menu guide -->
  <section class="tile row-1 col-1">
    <div class="photo photo-food" role="img" aria-label="Overhead spread of fresh fruit, vegetables and meat on a wooden table with a handwritten menu notebook"></div>
    <div class="panel panel-pink" style="left:156px;top:47px;width:140px;height:290px;">
      <span class="t c-cream" style="font-size:27px;">The Quick</span>
      <span class="t c-cream" style="font-size:38px;">Garden</span>
      <span class="t c-cream" style="font-size:32px;">Kitchen</span>
      <span class="t c-green" style="font-size:58px;">Menu</span>
      <span class="t c-green" style="font-size:58px;">Guide</span>
    </div>
  </section>

  <section class="tile row-1 col-2">
    <div class="photo photo-food" role="img" aria-label="Salmon steaks, tomatoes, avocado, eggs and lentils arranged around a wooden board"></div>
    <div class="panel panel-green" style="left:130px;top:67px;width:166px;height:234px;">
      <span class="t c-cream" style="font-size:20px;">The Quick</span>
      <span class="t c-cream" style="font-size:22px;">Garden Kitchen</span>
      <span class="t c-pink" style="font-size:62px;">Menu</span>
      <span class="t c-pink" style="font-size:62px;">Guide</span>
    </div>
  </section>

  <section class="tile row-1 col-3">
    <div class="photo photo-food" role="img" aria-label="Colourful frame of salmon, lentils, peppers, bananas and kiwi"></div>
    <div class="panel panel-green" style="left:59px;top:47px;width:177px;height:321px;">
      <span class="t c-cream" style="font-size:34px;">The Quick</span>
      <span class="t c-cream" style="font-size:44px;">Garden</span>
      <span class="t c-cream" style="font-size:34px;">Kitchen</span>
      <span class="t c-pink" style="font-size:66px;">Menu</span>
      <span class="t c-pink" style="font-size:66px;">Guide</span>
    </div>
  </section>

  <!-- Row 2: studio habits -->
  <section class="tile row-2 col-1">
    <div class="photo photo-friends-sky" role="img" aria-label="Two women sharing a whispered secret against a sky-blue backdrop"></div>
    <div class="fade-pink"></div>
    <div class="bottom-text" style="left:32px;bottom:24px;align-items:flex-start;">
      <span class="t c-green" style="font-size:29px;">Studio Habits</span>
      <span class="t c-cream" style="font-size:24px;margin-top:4px;">For Lasting Energy</span>
      <span class="script c-cream" style="font-size:36px;margin:4px 0 4px 18px;">Past Midlife</span>
      <span class="t c-cream" style="font-size:23px;">Zero Gym Needed</span>
    </div>
  </section>

  <section class="tile row-2 col-2">
    <div class="photo photo-friends-light" role="img" aria-label="Two women whispering, one smiling in surprise, on a bright white background"></div>
    <div class="fade-green"></div>
    <div class="bottom-text" style="align-items:center;bottom:18px;">
      <span class="t c-pink" style="font-size:28px;">Studio Habits</span>
      <span class="t c-cream" style="font-size:25px;margin-top:6px;">For Lasting Energy</span>
      <span class="t c-cream" style="font-size:40px;margin-top:6px;">Past Midlife</span>
      <span class="t c-cream" style="font-size:25px;margin-top:6px;">Zero Gym Needed</span>
    </div>
  </section>

  <section class="tile row-2 col-3">
    <div class="photo photo-friends-sky" role="img" aria-label="Two women sharing a whispered secret against a sky-blue backdrop"></div>
    <div class="panel panel-pink" style="left:79px;top:153px;width:137px;height:215px;">
      <span class="t c-cream" style="font-size:28px;">Studio</span>
      <span class="t c-cream" style="font-size:28px;">Habits</span>
      <span class="t c-green" style="font-size:20px;margin-top:3px;">For Lasting</span>
      <span class="t c-green" style="font-size:34px;">Energy</span>
      <span class="script c-green" style="font-size:22px;">Past Midlife</span>
      <span class="t c-green" style="font-size:22px;">Zero Gym</span>
      <span class="t c-green" style="font-size:22px;">Needed</span>
    </div>
  </section>

  <!-- Row 3: morning reboot -->
  <section class="tile row-3 col-1 soft-bg">
    <div class="cutout" style="left:60px;top:14px;width:176px;height:200px;" role="img" aria-label="Smiling woman in a white cropped sweater pointing to her waist"></div>
    <div class="arc"></div>
    <div class="bottom-text" style="align-items:center;bottom:14px;">
      <span class="t c-green" style="font-size:32px;">Ten-Week Bright</span>
      <span class="t c-cream" style="font-size:44px;">Morning</span>
      <span class="script c-cream" style="font-size:42px;">Reboot</span>
    </div>
  </section>

  <section class="tile row-3 col-2 soft-bg">
    <div style="position:absolute;left:0;right:0;top:20px;display:flex;flex-direction:column;align-items:center;">
      <span class="t c-green" style="font-size:33px;">Ten-Week Bright</span>
      <span class="t c-pink" style="font-size:44px;">Morning</span>
      <span class="script c-pink" style="font-size:38px;">Reboot</span>
    </div>
    <div class="cutout" style="left:70px;top:214px;width:156px;height:154px;" role="img" aria-label="Smiling woman in a white cropped sweater pointing to her waist"></div>
  </section>

  <section class="tile row-3 col-3">
    <div class="photo photo-kitchen" role="img" aria-label="Smiling woman in a white cropped sweater standing in a wood kitchen, pointing to her waist"></div>
    <div class="panel panel-pink" style="left:82px;top:203px;width:130px;height:165px;justify-content:flex-start;padding-top:4px;">
      <span class="t c-green" style="font-size:30px;">Ten-Week</span>
      <span class="t c-green" style="font-size:42px;">Bright</span>
      <span class="t c-cream" style="font-size:24px;margin-top:4px;">Morning</span>
      <span class="t c-cream" style="font-size:24px;">Reboot</span>
    </div>
  </section>

</main>
</body>
</html>
```